RTavenor Business Cards & Letterhead

I have a logo but need a design for some new business cards. We are a Design-Build Firm that specializes in the design and construction of commercial projects.
the cards need to be professional. no cartoon stuff.
i would like to have the cards in AI format so I can update the card as needed. Logo is provided.
Our Address is: 4187 Marlowe Ct. Alder, West Virginia 27614

```html
<!DOCTYPE html>
<html lang="en">
<head>
<meta charset="utf-8">
<title>RTavenor Business Card</title>
<link href="https://fonts.googleapis.com/css2?family=Montserrat:wght@400;500;700;800&display=swap" rel="stylesheet">
<style>
  :root {
    --backdrop: #d9d9db;
    --card-white: #f1f1f2;
    --brand-blue: #2f7db3;
    --deep-blue: #165f97;
    --light-blue: #6aa7cb;
    --emboss-blue: #4a93c4;
    --swoosh-gray: #4e4f54;
    --logo-gray: #3f4045;
    --text-gray: #5c5d61;
  }
  html, body {
    margin: 0;
    width: 1200px;
    height: 1200px;
    overflow: hidden;
    background: var(--backdrop);
    font-family: "Montserrat", sans-serif;
  }
  .canvas {
    position: relative;
    width: 1200px;
    height: 1200px;
  }
  .card {
    position: absolute;
    left: 160px;
    width: 880px;
    height: 503px;
    border-radius: 28px;
    overflow: hidden;
    box-shadow: 0 10px 28px rgba(0,0,0,0.18);
  }
  .card-back {
    top: 70px;
    background: linear-gradient(120deg, var(--light-blue) 0%, #2a86bd 45%, var(--deep-blue) 100%);
  }
  .back-wordmark {
    position: absolute;
    left: 0;
    right: 0;
    top: 50%;
    transform: translateY(-50%);
    text-align: center;
    font-weight: 800;
    font-size: 84px;
    letter-spacing: 2px;
    color: var(--emboss-blue);
  }
  .card-front {
    top: 627px;
    background: var(--card-white);
  }
  .swoosh {
    position: absolute;
    inset: 0;
    width: 880px;
    height: 503px;
  }
  .front-wordmark {
    position: absolute;
    right: 110px;
    top: 48px;
    font-weight: 800;
    font-size: 46px;
    letter-spacing: 1px;
    color: var(--logo-gray);
  }
  .holder-name {
    position: absolute;
    left: 62px;
    top: 92px;
    margin: 0;
    font-weight: 800;
    font-size: 40px;
    color: var(--brand-blue);
  }
  .holder-role {
    position: absolute;
    left: 76px;
    top: 146px;
    margin: 0;
    font-weight: 500;
    font-size: 22px;
    color: var(--text-gray);
  }
  .address {
    position: absolute;
    left: 100px;
    top: 270px;
    margin: 0;
    font-style: normal;
    font-weight: 500;
    font-size: 23px;
    line-height: 32px;
    color: var(--text-gray);
  }
  .contact-list {
    position: absolute;
    left: 104px;
    top: 352px;
    margin: 0;
    padding: 0;
    list-style: none;
  }
  .contact-item {
    display: flex;
    align-items: center;
    gap: 14px;
    height: 34px;
    font-weight: 500;
    font-size: 23px;
    color: var(--text-gray);
  }
  .contact-icon {
    width: 20px;
    height: 20px;
    flex: none;
  }
</style>
</head>
<body>
<main class="canvas">

  <section class="card card-back" aria-label="Card back">
    <div class="back-wordmark">RTAVENOR</div>
  </section>

  <section class="card card-front" aria-label="Card front">
    <svg class="swoosh" viewBox="0 0 880 503" aria-hidden="true">
      <path d="M800,0 C870,190 790,410 560,503 L880,503 L880,0 Z" fill="var(--swoosh-gray)"/>
      <path d="M880,120 C870,320 790,440 630,503 L880,503 Z" fill="var(--deep-blue)"/>
    </svg>

    <div class="front-wordmark">RTAVENOR</div>

    <h1 class="holder-name">Marcus Tavenor</h1>
    <p class="holder-role">President</p>

    <address class="address">4187 Marlowe Ct. Alder,<br>West Virginia 27614</address>

    <ul class="contact-list">
      <li class="contact-item">
        <svg class="contact-icon" viewBox="0 0 24 24" aria-hidden="true">
          <path d="M6.6 10.8a15.1 15.1 0 0 0 6.6 6.6l2.2-2.2a1 1 0 0 1 1-.25 11.4 11.4 0 0 0 3.6.57 1 1 0 0 1 1 1V20a1 1 0 0 1-1 1A17 17 0 0 1 3 4a1 1 0 0 1 1-1h3.5a1 1 0 0 1 1 1c0 1.25.2 2.45.57 3.570a1 1 0 0 1-.25 1z" fill="var(--brand-blue)"/>
        </svg>
        (919)-555-0148
      </li>
      <li class="contact-item">
        <svg class="contact-icon" viewBox="0 0 24 24" aria-hidden="true">
          <rect x="2" y="5" width="20" height="14" rx="1.5" fill="var(--brand-blue)"/>
          <path d="M3 6.5 12 13l9-6.5" fill="none" stroke="#ffffff" stroke-width="1.6"/>
        </svg>
        info@rtavenor.com
      </li>
      <li class="contact-item">
        <svg class="contact-icon" viewBox="0 0 24 24" aria-hidden="true">
          <circle cx="12" cy="12" r="10" fill="var(--brand-blue)"/>
          <path d="M2 12h20M12 2c3 3 3 17 0 20M12 2c-3 3-3 17 0 20" fill="none" stroke="#ffffff" stroke-width="1.4"/>
        </svg>
        www.rtavenor.com
      </li>
    </ul>
  </section>

</main>
</body>
</html>
```